Corvana Tongue Works, LLC

We need a business card that includes information about our business and conveys a reliable business that provides document translation services and interpreters for a variety of corporate and individual clients. We want to come across as professional, reliable, yet approachable. It should include the following on one side:

ESL / ENL Language Classes, Private Lessons, and Online Tutors
PLEXA Training and Testing
Translating & Interpreting Services
Contact us about Over-the-Phone Interpreting in over 200 languages
24/7/365
www.corvanatongue.example

The other side should include (555) 481-3062

Rhoda Pelling, President
482 Garnet Ave., Ste. 219
Indianapolis, IN 40917

Please add USA as part of the address. Also, please add rmpelling@corvanatongueworks.example as the e-mail address. Thank you.

Target Market(s)

Business professionals, their families, the international community

Industry/Entity Type

Business

Contact Information for Business Card

24/7/365
www.corvanatongue.example

(555) 481-3062

Rhoda Pelling, President
482 Garnet Ave., Ste. 219
Indianapolis, IN 40917
USA

Font styles to use
Sans Serif

Colors

Designer to choose colors to be used in the design.

Requirements
Must have
• See project description
• e-mail address and web address
• Phone number
Nice to have
• a globe
• physical address
Should not have
• Should not have the same color scheme as other agencies in our market in Indiana unless it is blue and black. No purple or yellow.

```html
<!DOCTYPE html>
<html lang="en">
<head>
<meta charset="utf-8">
<title>Corvana Tongue Works – Business Card</title>
<link href="https://fonts.googleapis.com/css2?family=Roboto+Condensed:wght@400;500;700&display=swap" rel="stylesheet">
<style>
  :root {
    --canvas: #d6d7d9;
    --navy-deep: #0b0f2a;
    --navy-mid: #151a44;
    --navy-glow: #1e2a66;
    --dot-blue: #1f5fb8;
    --brand-blue: #0a6bbf;
    --link-blue: #1d6fc0;
    --bullet-blue: #2a84d6;
    --icon-blue: #29a3e6;
    --muted-grey: #9a9a9a;
    --white: #ffffff;
  }
  * { margin: 0; padding: 0; box-sizing: border-box; }
  html, body { width: 1200px; height: 1000px; overflow: hidden; }
  body {
    background: var(--canvas);
    font-family: "Roboto Condensed", "Arial Narrow", sans-serif;
    position: relative;
  }

  /* ---------- Front ---------- */
  .card-front {
    position: absolute; left: 255px; top: 84px; width: 690px; height: 394px;
    background: var(--white); padding: 7px;
  }
  .card-front .face {
    position: relative; width: 100%; height: 100%; overflow: hidden;
    background: linear-gradient(180deg, var(--navy-deep) 0%, var(--navy-deep) 55%, var(--navy-mid) 85%, var(--navy-glow) 100%);
  }
  .globe-area { position: absolute; top: 0; width: 250px; height: 350px; }
  .globe-area.left {
    left: 0;
    background: radial-gradient(ellipse 75% 60% at 35% 50%, rgba(31,95,184,0.55) 0%, rgba(31,95,184,0.2) 55%, rgba(31,95,184,0) 100%);
  }
  .globe-area.right {
    right: 0;
    background: radial-gradient(ellipse 75% 60% at 65% 50%, rgba(31,95,184,0.55) 0%, rgba(31,95,184,0.2) 55%, rgba(31,95,184,0) 100%);
  }
  .front-brand {
    position: absolute; left: 0; right: 0; top: 168px;
    display: flex; align-items: center; justify-content: center; gap: 12px;
  }
  .brand-dot { width: 26px; height: 26px; border-radius: 50%; background: var(--white); flex: none; }
  .front-brand .brand-name {
    color: var(--white); font-size: 26px; font-weight: 500; letter-spacing: 0.5px;
  }
  .front-contact {
    position: absolute; left: 0; right: 0; bottom: 12px;
    text-align: center; color: var(--white);
  }
  .front-contact .contact-line {
    display: flex; align-items: center; justify-content: center; gap: 18px;
    margin-bottom: 6px;
  }
  .front-contact .phone {
    display: flex; align-items: center; gap: 4px;
    font-size: 17px; font-weight: 400; letter-spacing: 0.6px;
  }
  .front-contact .email {
    display: flex; align-items: center; gap: 6px;
    font-size: 13px; letter-spacing: 0.3px;
  }
  .front-contact .address {
    display: flex; align-items: center; justify-content: center; gap: 6px;
    font-size: 12.5px; text-transform: uppercase; letter-spacing: 0.3px;
  }
  .icon { fill: var(--icon-blue); flex: none; }

  /* ---------- Back ---------- */
  .card-back {
    position: absolute; left: 255px; top: 522px; width: 690px; height: 394px;
  }
  .card-back svg.frame { position: absolute; inset: 0; }
  .back-globe {
    position: absolute; left: 7px; top: 40px; width: 220px; height: 340px;
    background: radial-gradient(ellipse 70% 60% at 40% 55%, rgba(31,95,184,0.5) 0%, rgba(31,95,184,0.15) 60%, rgba(31,95,184,0) 100%);
  }
  .back-brand {
    position: absolute; left: 62px; top: 176px;
    display: flex; align-items: center; gap: 8px;
  }
  .back-brand .brand-dot { width: 62px; height: 62px; }
  .back-brand .brand-name {
    color: var(--white); font-size: 19px; font-weight: 400; line-height: 1.05; width: 110px;
  }
  .website {
    position: absolute; right: 20px; top: 18px;
    color: var(--link-blue); font-size: 13px; font-weight: 700;
  }
  .services {
    position: absolute; left: 340px; top: 156px; list-style: none;
    color: var(--bullet-blue); font-size: 16px; font-weight: 500; line-height: 22px;
  }
  .services li { position: relative; padding-left: 11px; margin-bottom: 4px; width: 320px; }
  .services li::before {
    content: ""; position: absolute; left: 0; top: 9px;
    width: 5px; height: 5px; border-radius: 50%; background: var(--muted-grey);
  }
  .phone-note {
    position: absolute; right: 20px; bottom: 19px;
    color: var(--muted-grey); font-size: 13.5px; font-weight: 700;
  }
  .phone-note .accent { color: var(--bullet-blue); }
</style>
</head>
<body>

  <section class="card-front" aria-label="Business card front">
    <div class="face">
      <div class="globe-area left" role="img" aria-label="Dotted world globe showing the Americas"></div>
      <div class="globe-area right" role="img" aria-label="Dotted world globe showing the Americas"></div>

      <div class="front-brand">
        <span class="brand-dot"></span>
        <span class="brand-name">Corvana Tongue Works</span>
      </div>

      <div class="front-contact">
        <div class="contact-line">
          <div class="phone">
            <svg class="icon" width="16" height="18" viewBox="0 0 24 24" aria-hidden="true">
              <path d="M6.6 10.8a15.1 15.1 0 0 0 6.6 6.6l2.2-2.2a1 1 0 0 1 1-.25 11.4 11.4 0 0 0 3.6.57 1 1 0 0 1 1 1V20a1 1 0 0 1-1 1A17 17 0 0 1 3 4a1 1 0 0 1 1-1h3.5a1 1 0 0 1 1 1c0 1.25.2 2.45.57 3.57a1 1 0 0 1-.25 1z"/>
            </svg>
            <span>(555) 481-3062</span>
          </div>
          <div class="email">
            <svg class="icon" width="16" height="12" viewBox="0 0 20 14" aria-hidden="true">
              <path d="M0 0h20v14H0zM1.5 1.5v.4L10 7.6l8.5-5.7v-.4zM1.5 3.7v8.8h17V3.7L10 9.4z"/>
            </svg>
            <span>rmpelling@corvanatongueworks.example</span>
          </div>
        </div>
        <div class="address">
          <svg class="icon" width="13" height="20" viewBox="0 0 12 18" aria-hidden="true">
            <path d="M6 0a6 6 0 0 0-6 6c0 4.5 6 12 6 12s6-7.5 6-12a6 6 0 0 0-6-6zm0 8.3A2.3 2.3 0 1 1 6 3.7a2.3 2.3 0 0 1 0 4.6z"/>
          </svg>
          <span>Rhoda Pelling, President 482 Garnet Ave., Ste. 219 Indianapolis, IN 40917 USA</span>
        </div>
      </div>
    </div>
  </section>

  <section class="card-back" aria-label="Business card back">
    <svg class="frame" width="690" height="394" viewBox="0 0 690 394" aria-hidden="true">
      <defs>
        <linearGradient id="panelFade" x1="0" y1="0" x2="1" y2="0">
          <stop offset="0" stop-color="#0b0f2a"/>
          <stop offset="0.55" stop-color="#111840"/>
          <stop offset="1" stop-color="#1b3f86"/>
        </linearGradient>
      </defs>
      <rect width="690" height="394" fill="#ffffff"/>
      <polygon points="363,0 690,0 690,394 195,394 199,386 683,386 683,8 360,8" fill="#0a6bbf"/>
      <polygon points="7,8 360,8 197,388 7,388" fill="url(#panelFade)"/>
    </svg>

    <div class="back-globe" role="img" aria-label="Dotted world globe showing the Americas"></div>

    <div class="back-brand">
      <span class="brand-dot"></span>
      <span class="brand-name">Corvana Tongue Works, LLC</span>
    </div>

    <div class="website">www.corvanatongue.example</div>

    <ul class="services">
      <li>ESL / ENL Language Classes, Private Lessons, and Online Tutors</li>
      <li>PLEXA Training and Testing</li>
      <li>Translating &amp; Interpreting Services</li>
    </ul>

    <p class="phone-note">Contact us about Over-the-Phone Interpreting in over <span class="accent">200</span> languages <span class="accent">24/7/365</span></p>
  </section>

</body>
</html>
```